Modern Medical Optometry Website

We need mordern, Patient friendly website. Easy to navigate and enhance our advance medical technology and excellent patient care.
1. HOME PAGE
2. OUR TEAM PAGE
3. EYECARE PAGE - VISION SERVICES, EYE EXAMS, KERATOCONUS CENTER, GLAUCOMA , DIABITES, MELORIDEX EXAM, DIGITAL RETINAL, OCT.
4. MYOPIA CONTROL CLINIC
5. DRY EYE CLINIC
6. EYEWEAR
7. PATIENT CENTER - BLOG
7. CONTACT US
This is our current website www.brivaloka.com
and We want to add more content and a cleaner design like these website
http://tarnwickfolvendale.com/
https://www.qmvorlu.com/

```html
<!DOCTYPE html>
<html lang="en">
<head>
<meta charset="utf-8">
<title>Lumora Optometry</title>
<link href="https://fonts.googleapis.com/css2?family=Raleway:wght@400;500;600;700;800&family=Open+Sans:wght@400;600&display=swap" rel="stylesheet">
<style>
:root{
  --teal:#0f8ca9;
  --teal-dark:#0b6f87;
  --yellow:#f5d817;
  --ink:#1c1c1c;
  --text:#6d6d6d;
  --pale:#e6f2f6;
  --grey-tab:#eeeeee;
  --footer:#141414;
  --footer-bottom:#050505;
  --white:#ffffff;
}
*{box-sizing:border-box;margin:0;padding:0}
html,body{width:1200px;height:3390px;overflow:hidden;background:var(--white)}
body{position:relative;font-family:"Open Sans",Arial,sans-serif;color:var(--text)}
.abs{position:absolute}

/* header */
.hero-photo{left:0;top:0;width:1200px;height:678px;background:linear-gradient(100deg,#e9d8cc 0%,#f2ebe6 35%,#f3f1ef 60%,#e6e4e2 100%)}
.nav-bar{left:77px;top:23px;width:1046px;height:101px;background:var(--teal);border-radius:6px;display:flex;align-items:center;padding:0 22px}
.brand{display:flex;align-items:center;gap:12px;color:var(--white);font-family:"Raleway",sans-serif;font-weight:600;font-size:20px;letter-spacing:1px;white-space:nowrap}
.brand-mark{width:34px;height:34px;border:3px solid var(--yellow);border-radius:4px}
.menu{display:flex;gap:26px;margin-left:auto;margin-right:24px;list-style:none}
.menu li{font-family:"Raleway",sans-serif;font-size:13px;font-weight:500;color:var(--white);letter-spacing:.2px;white-space:nowrap}
.menu li.active{color:var(--yellow)}
.hero-title{left:685px;top:240px;font-family:"Raleway",sans-serif;font-weight:800;font-size:64px;line-height:70px;color:var(--yellow);letter-spacing:1px;text-shadow:0 2px 4px rgba(0,0,0,.25);white-space:nowrap}
.hero-copy{left:685px;top:398px;width:430px;font-size:14px;line-height:25px;color:#555}
.btn{display:inline-flex;align-items:center;justify-content:center;border-radius:30px;font-family:"Raleway",sans-serif;font-weight:600;letter-spacing:.5px;white-space:nowrap}
.btn-teal{left:683px;top:506px;width:250px;height:50px;background:var(--teal);color:var(--white);font-size:16px}

/* services */
.about-band{left:0;top:678px;width:1200px;height:730px;background:var(--pale)}
.services{left:77px;top:658px;width:1046px;height:312px;display:flex}
.service{flex:1;background:var(--white);padding:30px 22px;border-right:1px solid #e4e4e4}
.service.featured{background:var(--teal)}
.service svg{width:58px;height:58px;display:block;margin-bottom:20px}
.service h3{font-family:"Raleway",sans-serif;font-weight:500;font-size:19px;line-height:28px;color:var(--teal);margin-bottom:14px}
.service p{font-size:13px;line-height:25px;color:#9a9a9a}
.service.featured h3,.service.featured p{color:var(--white)}
.arrow{top:780px}

.about-title{left:0;width:1200px;top:1030px;text-align:center;font-family:"Raleway",sans-serif;font-weight:700;font-size:32px;color:var(--ink)}
.about-copy{left:240px;width:720px;top:1095px;text-align:center;font-size:13.5px;line-height:26px;color:#7a7a7a}
.about-copy p+p{margin-top:18px}
.btn-yellow{left:517px;top:1293px;width:166px;height:50px;background:var(--yellow);color:#333;font-size:16px}

/* promise */
.promise-title{left:79px;top:1528px;font-family:"Raleway",sans-serif;font-weight:700;font-size:34px;color:var(--ink);white-space:nowrap}
.promise-copy{left:79px;top:1590px;width:430px;font-size:14px;line-height:27px;color:#7a7a7a}
.tabs{left:79px;top:1700px;width:425px;list-style:none}
.tabs li{height:50px;background:var(--grey-tab);margin-bottom:12px;display:flex;align-items:center;padding-left:16px;gap:20px;font-family:"Raleway",sans-serif;font-size:24px;color:#333}
.tabs li.active{background:var(--teal);color:var(--white)}
.tabs svg{width:36px;height:14px}
.promise-photo{left:581px;top:1474px;width:542px;height:533px;border-radius:26px;background:linear-gradient(160deg,#c9a26a 0%,#b98d52 50%,#9a6b35 100%)}

/* testimonial */
.testimonial-bg{left:0;top:2075px;width:1200px;height:563px;background:linear-gradient(180deg,#2a8fa6 0%,#1c7d96 45%,#0f6a84 100%)}
.testimonial-title{left:0;width:1200px;top:2128px;text-align:center;font-family:"Raleway",sans-serif;font-weight:700;font-size:38px;color:var(--yellow)}
.testimonial-card{left:237px;top:2210px;width:728px;height:366px;background:rgba(20,18,16,.85);border-radius:14px;text-align:center}
.avatar{position:absolute;left:322px;top:50px;width:84px;height:84px;border-radius:50%;border:4px solid var(--white);background:linear-gradient(160deg,#d8d2cc,#8d8a88)}
.client{position:absolute;left:0;width:100%;top:150px;font-family:"Raleway",sans-serif;font-weight:600;font-size:17px;color:var(--yellow)}
.quote{position:absolute;left:40px;width:648px;top:192px;font-size:13.5px;line-height:26px;color:#e8e8e8}
.dots{position:absolute;left:0;width:100%;top:300px;display:flex;justify-content:center;gap:8px}
.dots span{width:13px;height:13px;border-radius:50%;border:2px solid var(--yellow)}
.dots span.on{background:var(--yellow)}

/* eyewear */
.brands{left:79px;top:2700px;width:1044px;display:flex;justify-content:space-between;font-family:"Raleway",sans-serif;font-weight:700;font-size:23px;color:#111;letter-spacing:1px;white-space:nowrap}
.frames{top:2785px;width:260px;height:130px;border-radius:60px;background:linear-gradient(180deg,#f6f3ef,#e4ddd4)}

/* footer */
.footer{left:0;top:2960px;width:1200px;height:362px;background:var(--footer)}
.col{top:3022px;width:240px}
.col h4{font-family:"Raleway",sans-serif;font-weight:700;font-size:19px;color:var(--teal);letter-spacing:.5px;margin-bottom:26px;white-space:nowrap}
.item{display:flex;gap:24px;font-size:14px;line-height:26px;color:#ddd;margin-bottom:16px}
.item svg{flex:none;width:20px;height:20px;margin-top:3px}
.post{display:flex;gap:16px;margin-bottom:20px}
.post-photo{flex:none;width:76px;height:76px;border-radius:50%;background:linear-gradient(160deg,#e7d7cc,#b89b88)}
.post p{font-size:13px;line-height:23px;color:#eee}
.post small{font-size:12px;color:#bbb}
.news-copy{font-size:13px;line-height:25px;color:#ccc;margin-bottom:16px}
.email{display:flex;height:50px}
.email span{flex:1;background:#444;color:#ddd;font-size:14px;display:flex;align-items:center;padding-left:16px}
.email b{width:52px;background:var(--yellow);display:flex;align-items:center;justify-content:center}
.socials{display:flex;gap:14px;margin-top:22px}
.socials span{width:40px;height:40px;border-radius:50%;border:1px solid #555}
.copyright{left:0;top:3322px;width:1200px;height:68px;background:var(--footer-bottom);display:flex;align-items:center;justify-content:center;font-size:13px;color:#888}
.copyright b{color:var(--yellow);font-weight:600;margin:0 4px}
</style>
</head>
<body>

<div class="abs hero-photo" role="img" aria-label="Photo of a young boy in glasses covering one eye in front of an eye chart"></div>

<header class="abs nav-bar">
  <div class="brand"><span class="brand-mark"></span>LUMORA OPTOMETRY</div>
  <ul class="menu">
    <li class="active">HOME</li><li>OUR TEAM</li><li>EYE CARE</li><li>MYOPIA CONTROL CLINIC</li><li>EYEWEAR</li><li>BLOG</li><li>CONTACT US</li>
  </ul>
  <svg width="22" height="22" viewBox="0 0 22 22" fill="none" stroke="#f5d817" stroke-width="2.4"><circle cx="9" cy="9" r="7"/><path d="M14 14l6 6"/></svg>
</header>

<h1 class="abs hero-title">LUMORA<br>OPTOMETRY</h1>
<p class="abs hero-copy">Lorem ipsum dolor sit amet, consectetur adipiscing elit, sed aliqua. Ut enim ad minim veniam, quis nostrud exercitation ullamco laboris nisi ut aliquip ex ea commodo consequat.</p>
<span class="abs btn btn-teal">MAKE AN APPOINTMENT</span>

<div class="abs about-band"></div>

<section class="abs services">
  <div class="service">
    <svg viewBox="0 0 58 58" fill="none" stroke="#555" stroke-width="2"><circle cx="16" cy="34" r="10"/><circle cx="42" cy="34" r="10"/><path d="M26 34h6M29 10v14M20 16h18"/></svg>
    <h3>Comprehensive Eye Examinations</h3>
    <p>Our comprehensive eye examinations evaluate your eyes, both inside and out, for any...</p>
  </div>
  <div class="service">
    <svg viewBox="0 0 58 58" fill="none" stroke="#555" stroke-width="2"><path d="M4 32c10-14 40-14 50 0-10 14-40 14-50 0z"/><circle cx="29" cy="32" r="8"/><path d="M34 10l8-6"/></svg>
    <h3>Eye Infections, Eye Injuries, Dry Eyes</h3>
    <p>Our office provides emergency services for eye infections and eye injuries...</p>
  </div>
  <div class="service featured">
    <svg viewBox="0 0 58 58" fill="none" stroke="#f5d817" stroke-width="2"><ellipse cx="26" cy="30" rx="14" ry="20"/><ellipse cx="32" cy="28" rx="11" ry="17"/></svg>
    <h3>Contact Lenses</h3>
    <p>We have been fitting specialty contact lenses for years and have seen some incredible...</p>
  </div>
  <div class="service">
    <svg viewBox="0 0 58 58" fill="none" stroke="#555" stroke-width="2"><path d="M4 29c10-13 40-13 50 0-10 13-40 13-50 0z"/><circle cx="29" cy="29" r="7"/><path d="M6 14V6h8M44 6h8v8M52 44v8h-8M14 52H6v-8"/></svg>
    <h3>Retinal Camera</h3>
    <p>Our doctors specialize in the diagnosis and treatment of dry eye syndrome....</p>
  </div>
</section>
<svg class="abs arrow" style="left:46px" width="20" height="56" viewBox="0 0 20 56" fill="none" stroke="#0f8ca9" stroke-width="2"><path d="M18 2L3 28l15 26"/></svg>
<svg class="abs arrow" style="left:1134px" width="20" height="56" viewBox="0 0 20 56" fill="none" stroke="#333" stroke-width="2"><path d="M2 2l15 26L2 54"/></svg>

<h2 class="abs about-title">ABOUT LUMORA</h2>
<div class="abs about-copy">
  <p>Welcome to Lumora Optometry, where your vision and eye health are our sole priority. We take great pride in providing you with state-of-the-art eyecare matched with personal attention from our staff and doctors. Your quality of life is our goal and we believe that healthy eyesight is vital to achieving it.</p>
  <p>Our professional and personable staff is highly trained in helping you achieve and maintain healthy eyesight. Our optometrists have combined experiences and specialize in Orthokeratology (OrthoK), Ocular disease, Glaucoma diagnosis &amp; management.</p>
</div>
<span class="abs btn btn-yellow">READ MORE</span>

<h2 class="abs promise-title">THE LUMORA PROMISE</h2>
<p class="abs promise-copy">Lorem ipsum dolor sit amet, consectetur adipiscing elit, sed aliqua. Ut enim ad minim veniam, quis nostrud exercitation ullamco laboris nisi ut aliquip ex ea commodo consequat.</p>
<ul class="abs tabs">
  <li class="active"><svg viewBox="0 0 36 14" fill="none" stroke="currentColor" stroke-width="2"><path d="M0 7h33M27 1l6 6-6 6"/></svg>Dry Eyes</li>
  <li><svg viewBox="0 0 36 14" fill="none" stroke="currentColor" stroke-width="2"><path d="M0 7h33M27 1l6 6-6 6"/></svg>Team</li>
  <li><svg viewBox="0 0 36 14" fill="none" stroke="currentColor" stroke-width="2"><path d="M0 7h33M27 1l6 6-6 6"/></svg>Social</li>
  <li><svg viewBox="0 0 36 14" fill="none" stroke="currentColor" stroke-width="2"><path d="M0 7h33M27 1l6 6-6 6"/></svg>Exams</li>
</ul>
<div class="abs promise-photo" role="img" aria-label="Close-up photograph of an eye framed by a cracked golden texture"></div>

<div class="abs testimonial-bg" role="img" aria-label="Teal-toned photo of a patient at an eye examination device"></div>
<h2 class="abs testimonial-title">CLIENTS TESTIMONIAL</h2>
<div class="abs testimonial-card">
  <div class="avatar" role="img" aria-label="Client portrait"></div>
  <div class="client">- Client Name</div>
  <p class="quote">Lorem ipsum dolor sit amet, consectetur adipiscing elit, sed do eiusmod tempor incididunt ut labore et dolore magna aliqua. Ut enim ad minim veniam, quis nostrud exercitation ullamco laboris nisi ut aliquip ex ea commodo consequat.</p>
  <div class="dots"><span></span><span class="on"></span><span></span></div>
</div>

<div class="abs brands"><span>VELMORE</span><span>ARDEN KLAY</span><span>OSTRALINE</span><span>NOVETTA</span><span>BRISQUE</span><span>KESTREL</span></div>
<div class="abs frames" style="left:110px" role="img" aria-label="Gold round eyeglass frames"></div>
<div class="abs frames" style="left:470px" role="img" aria-label="Round brown tinted sunglasses"></div>
<div class="abs frames" style="left:830px" role="img" aria-label="Clear transparent eyeglass frames"></div>

<footer class="abs footer"></footer>
<div class="abs col" style="left:79px">
  <h4>LUMORA OPTOMETRY</h4>
  <div class="item"><svg viewBox="0 0 20 20" fill="#f5d817"><path d="M4 1l4 4-2 3c1 3 3 5 6 6l3-2 4 4-3 3C8 19 1 12 1 4z"/></svg>555-014-2010</div>
  <div class="item"><svg viewBox="0 0 20 20" fill="#f5d817"><rect x="3" y="1" width="14" height="6"/><rect x="1" y="7" width="18" height="8" rx="1"/><rect x="4" y="13" width="12" height="6"/></svg>555-014-2070</div>
  <div class="item"><svg viewBox="0 0 20 20" fill="#f5d817"><path d="M1 4h18v12H1z"/><path d="M1 4l9 7 9-7" stroke="#141414" stroke-width="1.5" fill="none"/></svg>info@brivaloka.com</div>
  <div class="item"><svg viewBox="0 0 20 20" fill="#f5d817"><path d="M10 1a6 6 0 0 1 6 6c0 5-6 12-6 12S4 12 4 7a6 6 0 0 1 6-6z"/><circle cx="10" cy="7" r="2" fill="#141414"/></svg>4120 Alder Row Blvd.,<br>Fernvale, CA 90417</div>
</div>
<div class="abs col" style="left:348px">
  <h4>CEDAR HOLLOW</h4>
  <div class="item"><svg viewBox="0 0 20 20" fill="#f5d817"><path d="M4 1l4 4-2 3c1 3 3 5 6 6l3-2 4 4-3 3C8 19 1 12 1 4z"/></svg>555-016-4020</div>
  <div class="item"><svg viewBox="0 0 20 20" fill="#f5d817"><path d="M1 4h18v12H1z"/><path d="M1 4l9 7 9-7" stroke="#141414" stroke-width="1.5" fill="none"/></svg>cedarhollow@brivaloka.com</div>
  <div class="item"><svg viewBox="0 0 20 20" fill="#f5d817"><path d="M10 1a6 6 0 0 1 6 6c0 5-6 12-6 12S4 12 4 7a6 6 0 0 1 6-6z"/><circle cx="10" cy="7" r="2" fill="#141414"/></svg>2087 Quillon St., Suite 4,<br>Cedar Hollow, CA 90452</div>
</div>
<div class="abs col" style="left:617px">
  <h4>BLOG UPDATES</h4>
  <div class="post"><div class="post-photo" role="img" aria-label="Blog post thumbnail"></div><div><p>Lorem Ipsum simply dummy text of the.</p><small>15 Feb 2019</small></div></div>
  <div class="post"><div class="post-photo" role="img" aria-label="Blog post thumbnail"></div><div><p>Lorem Ipsum simply dummy text of the.</p><small>15 Feb 2019</small></div></div>
</div>
<div class="abs col" style="left:884px">
  <h4>NEWSLETTER</h4>
  <p class="news-copy">To receive email releases, simply provide us with your email below</p>
  <div class="email"><span>Email</span><b><svg width="22" height="22" viewBox="0 0 22 22" fill="#141414"><path d="M1 10L21 1l-7 20-3-8z"/></svg></b></div>
  <div class="socials"><span></span><span></span><span></span><span></span></div>
</div>
<div class="abs copyright">Copyright ©<b>LUMORA OPTOMETRY</b>- 2019 . All right Reserved</div>

</body>
</html>
```